Support People to improve their image and well-being by provided personalised advise

We need a design for business cards that could be used for production on plano press. We build a new business in our region for advising mostly women (also men though) on style embracing several aspects including fashion, style, self-confidence and ultimately your internal and external image. The business card should be "classy", "french-style". The business is located in the french -speaking part of Switzerland, close to France. The name of the company is Lomu Grace

Target Market(s)

Service fees won't be cheap (medium to premium) thus we target mid-class to upper-class women (1st target) and men (2nd target)

Industry/Entity Type

Life Coaching

Contact Information for Business Card

Conseil en Image

+41 76 418 63 07
tovasel@lomu-grace.example
linkedin.example/in/sel-moran-tova

Logo Text

Lomu Grace

Colors

Designer to choose colors to be used in the design.

```html
<!DOCTYPE html>
<html lang="fr">
<head>
<meta charset="utf-8">
<title>Lomu Grace – Cartes de visite</title>
<link rel="stylesheet" href="https://fonts.googleapis.com/css2?family=Jost:wght@400&family=Caveat+Brush&display=swap">
<style>
  :root {
    --backdrop: #c4c4c4;
    --card: #363a3d;
    --gold-dark: #b38c63;
    --gold-light: #dcc09c;
    --silver: #c9cbcc;
    --text-light: #d6d7d8;
    --text-muted: #c2c4c5;
  }
  * { margin: 0; padding: 0; box-sizing: border-box; }
  html, body { width: 1200px; height: 576px; overflow: hidden; }
  body {
    background: var(--backdrop);
    position: relative;
    font-family: "Jost", sans-serif;
  }
  .card {
    position: absolute;
    top: 139px;
    width: 484px;
    height: 292px;
    background: var(--card);
    border-radius: 13px;
    overflow: hidden;
    box-shadow: 0 2px 6px rgba(0,0,0,0.25);
  }
  .card--front { left: 82px; }
  .card--back { left: 602px; width: 481px; }

  .brand { position: absolute; text-align: center; }
  .brand__dot {
    display: block;
    margin: 0 auto 14px;
    border-radius: 50%;
    background: linear-gradient(135deg, var(--gold-light), var(--gold-dark));
  }
  .brand__name {
    font-weight: 400;
    color: var(--text-light);
    letter-spacing: 0.2em;
    white-space: nowrap;
    text-transform: uppercase;
  }
  .card--front .brand { left: 0; right: 0; top: 108px; }
  .card--front .brand__dot { width: 58px; height: 58px; }
  .card--front .brand__name { font-size: 24px; }

  .card--back .brand { left: 262px; width: 196px; top: 40px; }
  .card--back .brand__dot { width: 56px; height: 56px; margin-bottom: 30px; }
  .card--back .brand__name { font-size: 23px; }

  .person { position: absolute; left: 29px; top: 38px; }
  .person__name {
    font-family: "Caveat Brush", cursive;
    font-size: 27px;
    color: var(--gold-dark);
    line-height: 1;
  }
  .person__role {
    margin-top: 6px;
    font-size: 12px;
    color: var(--text-muted);
    letter-spacing: 0.02em;
  }

  .contact { position: absolute; left: 32px; top: 204px; list-style: none; }
  .contact__item {
    display: flex;
    align-items: center;
    height: 18px;
    font-size: 13px;
    color: var(--text-muted);
  }
  .contact__icon { width: 11px; height: 11px; margin-right: 10px; fill: var(--text-muted); }

  .card__band { position: absolute; left: 0; bottom: 0; width: 481px; height: 30px; }
</style>
</head>
<body>
  <section class="card card--front">
    <div class="brand">
      <span class="brand__dot"></span>
      <p class="brand__name">Lomu Grace</p>
    </div>
  </section>

  <section class="card card--back">
    <div class="person">
      <p class="person__name">Tova Moran</p>
      <p class="person__role">Conseil en Image</p>
    </div>

    <div class="brand">
      <span class="brand__dot"></span>
      <p class="brand__name">Lomu Grace</p>
    </div>

    <ul class="contact">
      <li class="contact__item">
        <svg class="contact__icon" viewBox="0 0 12 12"><path d="M1 3c0-1 1-2 2-2h6c1 0 2 1 2 2v1H8V3H4v1H1z M2 5h8l1 6H1z M6 6.5a1.5 1.5 0 1 0 0.01 0z"/></svg>
        +41 76 418 63 07
      </li>
      <li class="contact__item">
        <svg class="contact__icon" viewBox="0 0 12 12"><path d="M0 2h12v8H0z" /><path d="M0.5 2.5l5.5 4 5.5-4" stroke="#363a3d" stroke-width="1" fill="none"/></svg>
        tovasel@lomu-grace.example
      </li>
      <li class="contact__item">
        <svg class="contact__icon" viewBox="0 0 12 12"><circle cx="6" cy="6" r="5.5"/><path d="M0.5 6h11M6 0.5v11M2 3h8M2 9h8" stroke="#363a3d" stroke-width="0.8" fill="none"/><ellipse cx="6" cy="6" rx="2.4" ry="5.5" stroke="#363a3d" stroke-width="0.8" fill="none"/></svg>
        www.lomu-grace.example
      </li>
    </ul>

    <svg class="card__band" viewBox="0 0 481 30" preserveAspectRatio="none" aria-hidden="true">
      <defs>
        <linearGradient id="goldBand" x1="0" y1="0" x2="1" y2="0">
          <stop offset="0" stop-color="#a98259"/>
          <stop offset="0.6" stop-color="#d2b48e"/>
          <stop offset="1" stop-color="#e2c7a3"/>
        </linearGradient>
      </defs>
      <rect x="0" y="19" width="481" height="11" fill="var(--silver)"/>
      <path d="M230 30 L248 5 Q251 1 257 1 L481 1 L481 30 Z" fill="url(#goldBand)"/>
    </svg>
  </section>
</body>
</html>
```